Coffeeshop menu for filter tip

We want to have a cannabis (coffeeshop) menu in the size 25mm wide x 60mm wide. Some examples attached.

it must have the following text:
Menu

WEED p/g
Oblivane €16
Cloudplum €14
Tide Runner €14
Quincefig €16
Mega Marsh €14
Grey Heron €14

HASH p/g
Tashar Amber €12
Pebble Frost€11
Lime Dunes €14
Ash Petal €10

Target Market(s)

tourist in Amsterdam

Requirements
Nice to have
• cannabis sign leaf
• No Cigarettes allowed symbol

```html
<!DOCTYPE html>
<html lang="en">
<head>
<meta charset="utf-8">
<title>Coffeeshop Menu</title>
<link href="https://fonts.googleapis.com/css2?family=Questrial&display=swap" rel="stylesheet">
<style>
  :root {
    --bg: #121312;
    --panel-weed: #1b1c1b;
    --panel-hash: #0b0b0b;
    --band: #000000;
    --yellow: #f8f163;
    --white: #ffffff;
    --skyline: #1f201f;
  }
  * { margin: 0; padding: 0; box-sizing: border-box; }
  html, body { width: 1200px; height: 2880px; overflow: hidden; background: var(--bg); }
  body { font-family: "Questrial", sans-serif; }
  .menu {
    position: relative; width: 1200px; height: 2880px; overflow: hidden;
    background:
      radial-gradient(ellipse 900px 1400px at -200px 1300px, #1d1e1d 0%, transparent 70%),
      radial-gradient(ellipse 900px 1200px at 1400px 2100px, #262726 0%, transparent 70%),
      var(--bg);
  }
  .leaf {
    position: absolute;
    background: radial-gradient(ellipse at center, rgba(248,241,99,0.95) 0%, rgba(248,241,99,0.55) 45%, rgba(248,241,99,0) 72%);
  }
  .leaf--top-left { left: -60px; top: -60px; width: 520px; height: 560px; }
  .leaf--mid-left { left: -90px; top: 1080px; width: 330px; height: 460px; }
  .leaf--mid-right { left: 830px; top: 1430px; width: 440px; height: 430px; }
  .leaf--bottom-right { left: 830px; top: 2220px; width: 440px; height: 460px; }

  .no-smoking {
    position: absolute; left: 216px; top: 42px; height: 64px;
    display: flex; align-items: center; gap: 28px;
    color: var(--white); font-size: 60px; letter-spacing: 12px; line-height: 1;
  }
  .section-title {
    position: absolute; display: flex; justify-content: space-between;
    color: var(--yellow); line-height: 1;
  }
  .section-title--weed { left: 440px; width: 700px; top: 170px; font-size: 138px; }
  .section-title--hash { left: 62px; width: 676px; top: 1525px; font-size: 138px; }

  .panel { position: absolute; }
  .panel--weed { left: 163px; top: 328px; width: 1037px; height: 1123px; background: var(--panel-weed); }
  .panel--hash { left: 0; top: 1674px; width: 1051px; height: 766px; background: var(--panel-hash); }

  .item { position: absolute; display: flex; align-items: center; height: 120px; font-size: 106px; line-height: 1; }
  .item__name { color: var(--yellow); letter-spacing: 2px; }
  .item__price { color: var(--white); letter-spacing: -2px; }
  .panel--weed .item { left: 48px; width: 965px; justify-content: space-between; }
  .panel--hash .item { left: 0; width: 1051px; }
  .panel--hash .item__price { width: 168px; text-align: right; font-size: 92px; }
  .panel--hash .item__name { margin-left: 72px; }

  .skyline {
    position: absolute; left: 0; top: 2448px; width: 1200px; height: 208px;
    background: linear-gradient(to bottom, rgba(31,32,31,0) 0%, var(--skyline) 45%, #161716 100%);
  }
  .footer {
    position: absolute; left: 0; top: 2656px; width: 1200px; height: 224px;
    background: var(--band);
  }
  .footer__title {
    position: absolute; left: 248px; width: 712px; top: 44px;
    display: flex; justify-content: space-between;
    color: var(--white); font-size: 150px; line-height: 1;
  }
</style>
</head>
<body>
<div class="menu">
  <div class="leaf leaf--top-left" role="img" aria-label="Yellow cannabis leaf decoration"></div>
  <div class="leaf leaf--mid-left" role="img" aria-label="Yellow cannabis leaf decoration"></div>
  <div class="leaf leaf--mid-right" role="img" aria-label="Yellow cannabis leaf decoration"></div>
  <div class="leaf leaf--bottom-right" role="img" aria-label="Yellow cannabis leaf decoration"></div>

  <div class="no-smoking">
    <span>NO CIGARETTES</span>
    <svg width="64" height="64" viewBox="0 0 64 64" aria-hidden="true">
      <circle cx="32" cy="32" r="28" fill="none" stroke="#fff" stroke-width="6"/>
      <rect x="14" y="30" width="30" height="8" fill="#fff"/>
      <rect x="46" y="30" width="4" height="8" fill="#fff"/>
      <line x1="12" y1="12" x2="52" y2="52" stroke="#fff" stroke-width="6"/>
    </svg>
  </div>

  <div class="section-title section-title--weed"><span>W</span><span>E</span><span>E</span><span>D</span></div>

  <section class="panel panel--weed">
    <div class="item" style="top:76px"><span class="item__name">OBLIVANE</span><span class="item__price">€16</span></div>
    <div class="item" style="top:252px"><span class="item__name">CLOUDPLUM</span><span class="item__price">€14</span></div>
    <div class="item" style="top:428px"><span class="item__name">TIDE RUNNER</span><span class="item__price">€14</span></div>
    <div class="item" style="top:604px"><span class="item__name">QUINCEFIG</span><span class="item__price">€16</span></div>
    <div class="item" style="top:780px"><span class="item__name">MEGA MARSH</span><span class="item__price">€14</span></div>
    <div class="item" style="top:956px"><span class="item__name">GREY HERON</span><span class="item__price">€14</span></div>
  </section>

  <div class="section-title section-title--hash"><span>H</span><span>A</span><span>S</span><span>H</span></div>

  <section class="panel panel--hash">
    <div class="item" style="top:79px"><span class="item__price">€12</span><span class="item__name">TASHAR AMBER</span></div>
    <div class="item" style="top:255px"><span class="item__price">€11</span><span class="item__name">PEBBLE FROST</span></div>
    <div class="item" style="top:431px"><span class="item__price">€14</span><span class="item__name">LIME DUNES</span></div>
    <div class="item" style="top:607px"><span class="item__price">€10</span><span class="item__name">ASH PETAL</span></div>
  </section>

  <div class="skyline" role="img" aria-label="Dark silhouette of the Amsterdam skyline"></div>

  <footer class="footer">
    <div class="footer__title"><span>M</span><span>E</span><span>N</span><span>U</span></div>
  </footer>
</div>
</body>
</html>
```